Flowmark Engineering Business Card

our company has just rebranded and taken on a new logo design. We now need to update our business cards with the new logo. This is also an opportunity to reformat and modernize our look. We are an engineering company so the look needs to be formal and professional yet it should look modern. Have a look at our current card and the new card should have the same information.

Target Market(s)

Engineering firms, government, mining companies

Industry/Entity Type

Mechanical Engineering

Contact Information for Business Card

see example attached

Requirements
Must have
• look professional and modern
Should not have
• should not include the office locations 'Brisbane, Sydney and Kuala Lumpur'
• you will find this on the example but it should not be included in these versions. please remove from your submissions and resubmit

```html
<!DOCTYPE html>
<html lang="en">
<head>
<meta charset="utf-8">
<title>Flowmark Engineering Business Card</title>
<link rel="stylesheet" href="https://fonts.googleapis.com/css2?family=Exo+2:wght@500;600;700&display=swap">
<style>
  :root {
    --brand-blue: #3a4aa2;
    --card-white: #ffffff;
    --ink: #2b2b2b;
    --ink-soft: #555555;
    --backdrop: #e4e4e4;
  }
  * { box-sizing: border-box; margin: 0; padding: 0; }
  html, body { width: 1200px; height: 949px; overflow: hidden; }
  body {
    background: var(--backdrop);
    font-family: "Exo 2", Arial, sans-serif;
    color: var(--ink);
    position: relative;
  }
  .card {
    position: absolute;
    left: 330px;
    width: 540px;
    height: 310px;
    background: var(--card-white);
    border-radius: 24px;
    overflow: hidden;
    box-shadow: 0 6px 18px rgba(0,0,0,0.12);
  }
  .card--back { top: 100px; display: flex; align-items: center; justify-content: center; }
  .card--front { top: 520px; }

  .wordmark { display: flex; align-items: center; gap: 14px; color: var(--brand-blue); font-weight: 600; }
  .wordmark__dot { width: 46px; height: 46px; border-radius: 50%; border: 5px solid currentColor; flex: none; }
  .wordmark__text { line-height: 1; }
  .wordmark__name { font-size: 34px; letter-spacing: 1px; text-transform: uppercase; }
  .wordmark__sub { font-size: 13px; letter-spacing: 7px; text-transform: uppercase; margin-top: 6px; }

  .front-band { position: absolute; inset: 0; width: 100%; height: 100%; }
  .front-band polygon { fill: var(--brand-blue); }

  .card--front .wordmark { position: absolute; left: 34px; top: 190px; color: var(--card-white); }
  .card--front .wordmark__name { font-size: 40px; }
  .card--front .wordmark__sub { font-size: 14px; letter-spacing: 9px; }
  .card--front .wordmark__dot { width: 54px; height: 54px; }

  .contact { position: absolute; font-size: 14px; line-height: 1.35; color: var(--ink); }
  .contact__icon { width: 30px; height: 30px; display: block; margin-bottom: 8px; }
  .contact__icon circle { fill: var(--brand-blue); }
  .contact__icon path { fill: var(--card-white); }

  .contact--person { left: 40px; top: 22px; }
  .contact--person .contact__icon { margin-left: 30px; }
  .person__name { font-size: 18px; font-weight: 600; letter-spacing: 1px; }
  .person__role { font-size: 9px; font-weight: 500; letter-spacing: 1px; color: var(--ink-soft); }

  .contact--address { left: 232px; top: 40px; }
  .contact--address .contact__icon { margin-left: 40px; }
  .contact--phone { left: 420px; top: 118px; text-align: left; }
  .contact--phone .contact__icon { margin-left: 66px; }
</style>
</head>
<body>

  <section class="card card--back" aria-label="Card back">
    <div class="wordmark">
      <span class="wordmark__dot"></span>
      <div class="wordmark__text">
        <div class="wordmark__name">Flowmark</div>
        <div class="wordmark__sub">Engineering</div>
      </div>
    </div>
  </section>

  <section class="card card--front" aria-label="Card front">
    <svg class="front-band" viewBox="0 0 540 310" preserveAspectRatio="none" aria-hidden="true">
      <polygon points="0,128 405,128 425,310 0,310"/>
    </svg>

    <div class="contact contact--person">
      <svg class="contact__icon" viewBox="0 0 30 30" aria-hidden="true">
        <circle cx="15" cy="15" r="15"/>
        <path d="M15 8a4 4 0 1 1 0 8a4 4 0 1 1 0-8zM8 22c1-4 4-5 7-5s6 1 7 5z"/>
      </svg>
      <div class="person__name">JOHN DOE</div>
      <div class="person__role">INTERIOR DESIGNER</div>
    </div>

    <div class="contact contact--address">
      <svg class="contact__icon" viewBox="0 0 30 30" aria-hidden="true">
        <circle cx="15" cy="15" r="15"/>
        <path d="M15 7a6 6 0 0 1 6 6c0 4-6 10-6 10s-6-6-6-10a6 6 0 0 1 6-6zm0 3.5a2.5 2.5 0 1 0 0 5a2.5 2.5 0 1 0 0-5z"/>
      </svg>
      <div>214, 9th floor, Harbor</div>
      <div>Lane Road NTX</div>
    </div>

    <div class="contact contact--phone">
      <svg class="contact__icon" viewBox="0 0 30 30" aria-hidden="true">
        <circle cx="15" cy="15" r="15"/>
        <path d="M11 7h8a1 1 0 0 1 1 1v14a1 1 0 0 1-1 1h-8a1 1 0 0 1-1-1V8a1 1 0 0 1 1-1zm1 2v10h6V9zm3 11a1 1 0 1 0 0 2a1 1 0 1 0 0-2z"/>
      </svg>
      <div>012 555 0198</div>
      <div>012 555 0198</div>
    </div>

    <div class="wordmark">
      <span class="wordmark__dot"></span>
      <div class="wordmark__text">
        <div class="wordmark__name">Flowmark</div>
        <div class="wordmark__sub">Engineering</div>
      </div>
    </div>
  </section>

</body>
</html>
```